Redesign of business card for Cedar Ridge Mechanical

We are looking for a new design for our business cards for Cedar Ridge Mechanical. We are a plumbing & HVAC construction company, operating on the West Coast of Canada and USA. Logo attached.
Industry/Entity Type
Construction - Plumbing & HVAC
Contact Information for Business Card
Name, address, phone numbers, email, website address
Look and feel
Each slider illustrates characteristics of the customer's brand and the style your logo design should communicate.

```html
<!DOCTYPE html>
<html lang="en">
<head>
<meta charset="utf-8">
<title>Cedar Ridge Mechanical — Business Card</title>
<link href="https://fonts.googleapis.com/css2?family=Montserrat:wght@400;500;700&display=swap" rel="stylesheet">
<style>
  :root {
    --page-bg: #161616;
    --card-black: #1c1c1c;
    --card-white: #ffffff;
    --ink: #111111;
    --ink-soft: #6d6d6d;
    --rule: #8a8a8a;
    --swoosh: #9a9a9a;
    --mark-white: #ffffff;
  }
  * { box-sizing: border-box; margin: 0; padding: 0; }
  html, body {
    width: 1200px; height: 963px; overflow: hidden;
    background: var(--page-bg);
    font-family: "Montserrat", sans-serif;
  }
  .canvas {
    position: relative; width: 1200px; height: 963px;
    display: flex; flex-direction: column; align-items: center; justify-content: center; gap: 60px;
  }
  .card {
    position: relative; width: 600px; height: 343px;
    border-radius: 22px; overflow: hidden;
    box-shadow: 0 18px 40px rgba(0,0,0,.55);
  }
  .card--front { background: var(--card-white); }
  .card--back { background: var(--card-black); display: flex; align-items: center; justify-content: center; }
  .front-curve { position: absolute; inset: 0; width: 100%; height: 100%; }
  .contact {
    position: absolute; left: 44px; top: 40px; width: 300px; color: var(--ink);
  }
  .contact__name { font-weight: 700; font-size: 25px; letter-spacing: .5px; line-height: 1; }
  .contact__name .surname { color: var(--ink-soft); }
  .contact__role { font-size: 15px; color: var(--ink-soft); margin-top: 4px; }
  .contact__rule { height: 1px; background: var(--rule); width: 250px; margin: 18px 0; }
  .contact__address { font-size: 16px; color: var(--ink-soft); line-height: 1.25; }
  .contact__list { list-style: none; font-size: 15px; line-height: 1.5; }
  .contact__list li { display: flex; align-items: center; gap: 8px; white-space: nowrap; }
  .contact__list svg { width: 13px; height: 13px; flex: none; }
  .brand {
    display: flex; align-items: center; gap: 12px;
    color: var(--mark-white); font-weight: 700; text-transform: uppercase;
  }
  .brand__square { width: 20px; height: 20px; border: 3px solid var(--mark-white); flex: none; }
  .brand--front { position: absolute; left: 372px; top: 160px; font-size: 16px; line-height: 1.2; width: 210px; }
  .brand--back { font-size: 28px; letter-spacing: 1px; }
  .brand--back .brand__square { width: 30px; height: 30px; border-width: 4px; }
</style>
</head>
<body>
<main class="canvas">
  <section class="card card--front" aria-label="Business card front">
    <svg class="front-curve" viewBox="0 0 600 343" preserveAspectRatio="none" aria-hidden="true">
      <path d="M600 0 L600 343 L300 343 C300 200 390 40 600 0 Z" fill="#9a9a9a"/>
      <path d="M600 0 L600 343 L314 343 C318 190 410 45 600 0 Z" fill="#1c1c1c"/>
    </svg>
    <div class="contact">
      <p class="contact__name">DANIEL <span class="surname">HARPER</span></p>
      <p class="contact__role">Manager</p>
      <div class="contact__rule"></div>
      <p class="contact__address">Your address, city<br>state, ZIP 0000</p>
      <div class="contact__rule"></div>
      <ul class="contact__list">
        <li><svg viewBox="0 0 16 16"><path d="M3 1h3l1.5 4-2 1.2a9 9 0 0 0 4.3 4.3l1.2-2 4 1.5v3a2 2 0 0 1-2 2A13 13 0 0 1 1 3a2 2 0 0 1 2-2z" fill="#111"/></svg>604-555-0147</li>
        <li><svg viewBox="0 0 16 16"><rect x="1" y="3" width="14" height="10" rx="1" fill="#111"/><path d="M1.5 4 8 9l6.5-5" stroke="#fff" stroke-width="1.3" fill="none"/></svg>daniel@cedarridgemech.com</li>
        <li><svg viewBox="0 0 16 16"><circle cx="8" cy="8" r="7" fill="#111"/><path d="M1 8h14M8 1c-3 3-3 11 0 14M8 1c3 3 3 11 0 14" stroke="#fff" stroke-width="1" fill="none"/></svg>www.cedarridgemech.com</li>
      </ul>
    </div>
    <div class="brand brand--front">
      <span class="brand__square" aria-hidden="true"></span>
      <span class="brand__name">Cedar Ridge Mechanical</span>
    </div>
  </section>

  <section class="card card--back" aria-label="Business card back">
    <div class="brand brand--back">
      <span class="brand__square" aria-hidden="true"></span>
      <span class="brand__name">Cedar Ridge Mechanical</span>
    </div>
  </section>
</main>
</body>
</html>
```